Billboard design 8x3M RAVU (Spanish company)

We´re located in the south of Spain. We run a local telecom company.
We sell Fiber optic, and mobile phone lines mainly.
The billboard will have to be in Spanish, I would like the price to be something you spot on first sight when passing by in the car.
Our company color is blue, like in our logo which I will add. I will also add a example from what we currently have.
The new offer should be:
1000 megas + 100Gigas movil con llamadas ilimitadas. (meaning 1000Mb fiber optic speed and 100Gb data and unlimited calls for 1 mobile line)
Our details are: phone line 958 47 6620
Website: ra-vu.es

```html
<!DOCTYPE html>
<html lang="es">
<head>
<meta charset="utf-8">
<title>RAVU – Valla publicitaria 8x3</title>
<link rel="stylesheet" href="https://fonts.googleapis.com/css2?family=Exo+2:wght@600;700;800&family=Outfit:wght@700;900&display=swap">
<style>
  :root {
    --navy: #0d4a7a;
    --navy-deep: #0a3d66;
    --sky: #19b6ec;
    --sun: #fdd452;
    --white: #ffffff;
    --stage: #eef1f4;
    --photo-a: #e9d9c4;
    --photo-b: #9fb8cf;
    --photo-c: #c89a3c;
  }
  * { margin: 0; padding: 0; box-sizing: border-box; }
  html, body { width: 1200px; height: 874px; overflow: hidden; background: var(--stage); }
  .billboard {
    position: absolute; left: 20px; top: 227px;
    width: 1160px; height: 420px;
    background: var(--white); overflow: hidden;
    font-family: "Exo 2", sans-serif;
  }
  .lifestyle-photo {
    position: absolute; left: 620px; top: 0; width: 540px; height: 400px;
    background:
      linear-gradient(90deg, var(--white) 0%, rgba(255,255,255,0) 32%),
      radial-gradient(ellipse at 72% 55%, var(--photo-b) 0%, rgba(159,184,207,0) 55%),
      radial-gradient(ellipse at 45% 40%, var(--photo-c) 0%, rgba(200,154,60,0) 45%),
      linear-gradient(160deg, var(--photo-a), #d8dde2 60%, #b9c7d4);
  }
  .price-badge { position: absolute; left: 0; top: 0; width: 560px; height: 220px; }
  .price {
    position: absolute; left: 277px; top: 22px; transform: translateX(-50%);
    font-family: "Outfit", sans-serif; font-weight: 900; font-size: 96px; line-height: 1;
    color: var(--navy-deep); letter-spacing: -2px; white-space: nowrap;
  }
  .price-note {
    position: absolute; left: 277px; top: 122px; transform: translateX(-50%);
    font-family: "Outfit", sans-serif; font-weight: 700; font-size: 23px;
    color: var(--navy-deep); white-space: nowrap;
  }
  .brand { position: absolute; left: 492px; top: 20px; }
  .brand-name {
    display: flex; align-items: center; gap: 10px;
    font-weight: 800; font-size: 66px; line-height: 1; color: var(--sky); letter-spacing: 2px;
  }
  .brand-dot { width: 22px; height: 22px; border-radius: 50%; background: var(--sky); }
  .brand-services {
    margin-top: 10px; font-weight: 700; font-size: 20px; color: var(--sky); letter-spacing: .3px;
  }
  .offer { position: absolute; left: 40px; top: 212px; }
  .offer-main {
    font-weight: 800; font-size: 54px; line-height: 1; color: var(--navy-deep); letter-spacing: -.5px;
  }
  .offer-sub {
    margin-top: 8px; font-weight: 700; font-size: 37px; line-height: 1; color: var(--sky);
  }
  .contact-band { position: absolute; left: 0; top: 0; width: 1160px; height: 420px; }
  .contact {
    position: absolute; left: 32px; top: 356px;
    display: flex; align-items: center; gap: 12px; color: var(--white);
    font-weight: 700; line-height: 1;
  }
  .contact-icon { width: 40px; height: 40px; border-radius: 50%; background: var(--sky);
    display: flex; align-items: center; justify-content: center; }
  .contact-phone { font-size: 52px; letter-spacing: -.5px; margin-right: 8px; }
  .contact-web { font-size: 48px; margin-top: -12px; }
</style>
</head>
<body>
  <div class="billboard">
    <div class="lifestyle-photo" role="img" aria-label="Fotografía de una pareja sonriente en el sofá mirando un móvil con tazas de café"></div>

    <svg class="price-badge" viewBox="0 0 560 220" aria-hidden="true">
      <circle cx="277" cy="32" r="168" fill="none" stroke="var(--sky)" stroke-width="2.5" stroke-dasharray="8 7"/>
      <circle cx="277" cy="32" r="155" fill="var(--sun)"/>
    </svg>
    <div class="price">35€</div>
    <div class="price-note">Por sólo</div>

    <div class="brand">
      <div class="brand-name"><span class="brand-dot"></span>RAVU</div>
      <div class="brand-services">Wifi | Fibra | Movil | Tv</div>
    </div>

    <div class="offer">
      <div class="offer-main">1000 MEGAS + 100GIGAS</div>
      <div class="offer-sub">MOVIL CON LLAMADAS ILIMITADAS</div>
    </div>

    <svg class="contact-band" viewBox="0 0 1160 420" aria-hidden="true">
      <path d="M0 336 L690 330 C745 328 770 340 800 362 C830 384 860 388 900 388 L1160 388 L1160 420 L0 420 Z" fill="var(--sun)"/>
      <path d="M0 342 L690 336 C740 334 760 346 790 368 C820 390 850 394 900 394 L1160 394 L1160 420 L0 420 Z" fill="var(--navy)"/>
    </svg>

    <div class="contact">
      <span class="contact-icon">
        <svg width="22" height="22" viewBox="0 0 24 24"><path fill="#fff" d="M6.6 10.8a15.1 15.1 0 0 0 6.6 6.6l2.2-2.2c.3-.3.7-.4 1-.2 1.1.4 2.3.6 3.6.6.6 0 1 .4 1 1V20c0 .6-.4 1-1 1A17 17 0 0 1 3 4c0-.6.4-1 1-1h3.5c.6 0 1 .4 1 1 0 1.3.2 2.5.6 3.6.1.3 0 .7-.2 1z"/></svg>
      </span>
      <span class="contact-phone">958 47 6620</span>
      <span class="contact-icon">
        <svg width="22" height="22" viewBox="0 0 24 24"><rect x="5" y="5" width="14" height="10" rx="1" fill="none" stroke="#fff" stroke-width="2"/><rect x="2" y="17" width="20" height="2.5" rx="1" fill="#fff"/></svg>
      </span>
      <span class="contact-web">ra-vu.es</span>
    </div>
  </div>
</body>
</html>
```